Business Card Design for company

We want new business cards. We'd like something different-- yet still highly professional. Our tagline is Providing leadership, delivering success. Stock photos are ok, as long as they are relevant and look upscale.

Target Market(s)

Architecture/Business Management Consulting/Engineering Consulting

Contact Information for Business Card

dark gray background with pops of blue might be good, but you tell me. You're the designers. Rounded corners might be nice, but again, you tell me.

Font styles to use
Serif
Sans Serif

Colors
3276b5
5c5c5c
9d9d9d
fbfbfb

Requirements
Nice to have
• Something different, but still very professional.

```html
<!DOCTYPE html>
<html lang="en">
<head>
<meta charset="utf-8">
<title>Halvorn Partners – Business Card</title>
<link href="https://fonts.googleapis.com/css2?family=Montserrat:wght@400;500;600;700&display=swap" rel="stylesheet">
<style>
  :root {
    --stage: #1c1c1e;
    --blue: #3276b5;
    --blue-deep: #224f7a;
    --blue-mid: #2a5f95;
    --ink: #5c5c5c;
    --ink-dark: #3f4246;
    --muted: #9d9d9d;
    --paper: #fbfbfb;
    --paper-shade: #ececec;
  }
  * { margin: 0; padding: 0; box-sizing: border-box; }
  html, body {
    width: 1200px; height: 900px; overflow: hidden;
    background: var(--stage);
    font-family: "Montserrat", sans-serif;
  }
  .stage {
    width: 1200px; height: 900px;
    display: flex; align-items: center; justify-content: center; gap: 40px;
  }
  .card {
    width: 540px; height: 310px;
    border-radius: 30px;
    position: relative;
    overflow: hidden;
  }
  /* Front */
  .card--front {
    background: linear-gradient(160deg, var(--blue-deep) 0%, var(--blue-mid) 100%);
    color: var(--paper);
    display: flex; flex-direction: column; align-items: center; justify-content: center;
  }
  .front__name {
    font-size: 44px; font-weight: 600; letter-spacing: 1px;
    color: var(--paper);
  }
  .front__rule {
    width: 46px; height: 4px; background: var(--paper);
    margin: 34px 0 40px;
  }
  .front__tagline {
    font-size: 15px; font-weight: 500; letter-spacing: 0.6px;
    color: var(--paper);
  }
  /* Back */
  .card--back {
    background: linear-gradient(135deg, var(--paper) 0%, var(--paper-shade) 100%);
    color: var(--ink-dark);
  }
  .back__brand {
    position: absolute; top: 58px; left: 0; right: 0;
    text-align: center;
    font-size: 36px; font-weight: 600; letter-spacing: 1px;
    color: var(--blue);
  }
  .back__details {
    position: absolute; top: 148px; left: 0; right: 0;
    display: flex; justify-content: center; align-items: center; gap: 16px;
  }
  .person { text-align: right; }
  .person__name {
    font-size: 21px; font-weight: 700; letter-spacing: 0.5px;
    color: var(--blue);
  }
  .person__title { font-size: 15px; font-weight: 500; color: var(--ink-dark); }
  .divider { width: 1.5px; height: 60px; background: var(--blue); }
  .contacts { list-style: none; font-size: 13px; font-weight: 500; color: var(--ink-dark); }
  .contacts li { display: flex; align-items: center; gap: 7px; line-height: 20px; }
  .contacts svg { width: 12px; height: 12px; flex: none; }
  .back__address {
    position: absolute; bottom: 42px; left: 0; right: 0;
    text-align: center; font-size: 14px; font-weight: 500; color: var(--ink-dark);
  }
</style>
</head>
<body>
<main class="stage">
  <section class="card card--front" aria-label="Card front">
    <div class="front__name">Halvorn Partners</div>
    <div class="front__rule"></div>
    <p class="front__tagline">Providing leadership, delivering success</p>
  </section>

  <section class="card card--back" aria-label="Card back">
    <div class="back__brand">Halvorn Partners</div>
    <div class="back__details">
      <div class="person">
        <div class="person__name">DANIEL ROURKE</div>
        <div class="person__title">CEO &amp; Founder</div>
      </div>
      <div class="divider"></div>
      <ul class="contacts">
        <li>
          <svg viewBox="0 0 24 24" aria-hidden="true"><path fill="#3276b5" d="M6.6 10.8a15.1 15.1 0 0 0 6.6 6.6l2.2-2.2a1 1 0 0 1 1-.25 11.4 11.4 0 0 0 3.6.57 1 1 0 0 1 1 1V20a1 1 0 0 1-1 1A17 17 0 0 1 3 4a1 1 0 0 1 1-1h3.5a1 1 0 0 1 1 1c0 1.25.2 2.45.57 3.57a1 1 0 0 1-.25 1z"/></svg>
          (555) 014.2290
        </li>
        <li>
          <svg viewBox="0 0 24 24" aria-hidden="true"><rect x="3" y="5" width="18" height="14" rx="1.5" fill="none" stroke="#3276b5" stroke-width="2"/><path d="M3.5 6l8.5 7 8.5-7" fill="none" stroke="#3276b5" stroke-width="2"/></svg>
          info@halvornpartners.com
        </li>
        <li>
          <svg viewBox="0 0 24 24" aria-hidden="true"><circle cx="12" cy="12" r="9" fill="none" stroke="#3276b5" stroke-width="2"/><path d="M3 12h18M12 3c3 3.2 3 14.8 0 18M12 3c-3 3.2-3 14.8 0 18" fill="none" stroke="#3276b5" stroke-width="1.6"/></svg>
          www.halvornpartners.com
        </li>
      </ul>
    </div>
    <p class="back__address">820 Alder Row Suite 210, Fairview, AZ 85099</p>
  </section>
</main>
</body>
</html>
```